Ward Compass Business Card Design*

We need a business card design for our company Ward Compass. Our company is specialized in providing online consulting services regarding medical institutions, hospitals and doctors. We work with patients worldwide looking to choose between healthcare providers. We have a website you may use as a reference, where we list doctors and clinics worldwide. So we target Medical providers as well as patients worldwide.
Target Market(s)
Medical Providers and patients around the world
Industry/Entity Type
Medical
Contact Information for Business Card
Salwa Kettani
CEO
+90 612 348 2175
info@wardcompass.example
www.wardcompass.example
14 Annakhil 7 H.R.B. Rabat, Morocco
Requirements
Must have
- Company logo/name on one full side, personal info and smaller logo and company name on the other side.
Nice to have
- Smart and elegant design

```html
<!DOCTYPE html>
<html lang="en">
<head>
<meta charset="utf-8">
<title>Ward Compass Business Card</title>
<link rel="stylesheet" href="https://fonts.googleapis.com/css2?family=Montserrat:wght@400;500;700&display=swap">
<style>
  :root {
    --bg: #2a2b2f;
    --navy: #133a64;
    --navy-deep: #0f3560;
    --grey: #8a8b8d;
    --white: #ffffff;
    --ink: #3d3f44;
  }
  * { box-sizing: border-box; margin: 0; padding: 0; }
  html, body { width: 1200px; height: 800px; overflow: hidden; }
  body {
    background: var(--bg);
    font-family: "Montserrat", Arial, sans-serif;
    display: flex;
    align-items: center;
    justify-content: center;
    gap: 40px;
  }
  .card {
    position: relative;
    width: 540px;
    height: 309px;
    overflow: hidden;
    box-shadow: 0 14px 30px rgba(0,0,0,.45);
  }
  .card-front {
    background: var(--navy);
    display: flex;
    align-items: center;
    justify-content: center;
  }
  .brand {
    display: flex;
    align-items: center;
    gap: 14px;
  }
  .brand-dot {
    border-radius: 50%;
    flex: none;
  }
  .brand-name {
    font-weight: 700;
    letter-spacing: 1.5px;
    text-transform: uppercase;
  }
  .card-front .brand-dot { width: 44px; height: 44px; border: 6px solid var(--white); }
  .card-front .brand-name { color: var(--white); font-size: 28px; }

  .card-back { background: var(--white); }
  .card-back .backdrop { position: absolute; inset: 0; width: 100%; height: 100%; }
  .card-back .brand {
    position: absolute;
    left: 40px;
    top: 120px;
  }
  .card-back .brand-dot { width: 40px; height: 40px; border: 6px solid var(--navy); }
  .card-back .brand-name { color: var(--navy); font-size: 24px; }

  .person { position: absolute; left: 40px; top: 200px; }
  .person-name { font-size: 15px; color: var(--navy); letter-spacing: .5px; }
  .person-name strong { font-weight: 700; }
  .person-role { font-size: 11px; color: var(--ink); margin-top: 2px; }

  .contacts {
    position: absolute;
    left: 40px;
    top: 244px;
    list-style: none;
    font-size: 10.5px;
    color: var(--ink);
  }
  .contacts li { display: flex; align-items: center; gap: 7px; height: 17px; }
  .contact-icon {
    width: 13px; height: 13px; border-radius: 50%;
    background: var(--navy);
    display: flex; align-items: center; justify-content: center;
    flex: none;
  }
  .contact-icon svg { width: 8px; height: 8px; }
</style>
</head>
<body>
  <section class="card card-front" aria-label="Card front">
    <div class="brand">
      <span class="brand-dot"></span>
      <span class="brand-name">Ward Compass</span>
    </div>
  </section>

  <section class="card card-back" aria-label="Card back">
    <svg class="backdrop" viewBox="0 0 540 309" preserveAspectRatio="none" aria-hidden="true">
      <rect width="540" height="309" fill="var(--navy)"/>
      <circle cx="184" cy="340" r="420" fill="var(--white)"/>
      <circle cx="180" cy="340" r="412" fill="var(--grey)"/>
      <circle cx="158" cy="340" r="402" fill="var(--white)"/>
    </svg>

    <div class="brand">
      <span class="brand-dot"></span>
      <span class="brand-name">Ward Compass</span>
    </div>

    <div class="person">
      <p class="person-name"><strong>SALWA</strong> KETTANI</p>
      <p class="person-role">CEO</p>
    </div>

    <ul class="contacts">
      <li>
        <span class="contact-icon"><svg viewBox="0 0 10 10"><path d="M2 1l2 2-1 1.2c.6 1.2 1.6 2.2 2.8 2.8L7 6l2 2-1.3 1.3C4.5 9 1 5.5.7 2.3z" fill="#fff"/></svg></span>
        +90 612 348 2175
      </li>
      <li>
        <span class="contact-icon"><svg viewBox="0 0 10 10"><rect x="1" y="2.2" width="8" height="5.6" fill="#fff"/><path d="M1 2.2l4 3 4-3" stroke="var(--navy)" stroke-width=".9" fill="none"/></svg></span>
        info@wardcompass.example
      </li>
      <li>
        <span class="contact-icon"><svg viewBox="0 0 10 10"><circle cx="5" cy="5" r="4" stroke="#fff" fill="none"/><path d="M1 5h8M5 1c-2 2.5-2 5.5 0 8M5 1c2 2.5 2 5.5 0 8" stroke="#fff" stroke-width=".8" fill="none"/></svg></span>
        www.wardcompass.example
      </li>
    </ul>
  </section>
</body>
</html>
```